Kelvor Engineers: Why you should hire us keepsake

New design. Open to plastic cards. We are an engineering firm that designs cell phone towers and commercial buildings. Please check out our website www.kelvorstruct.com for more details. We want people to remember our card and for it to be useful if possible. We want the same look and feel on these cards to be translated to other marketing material we may need such as brochures.

Target Market(s)

Architects, Developers and Telecommunication Carriers

Industry/Entity Type

Engineering

Contact Information for Business Card

Card with our company colors, logo, and innovative design with elements related to our industry.

Font styles to use
Sans Serif

Colors
9bcb3c
abd036
0255a3

Requirements
Must have
• Sleek and hip design
Nice to have
• Bright lime green and navy coloring that pops with an innovative design.
Should not have
• A basic and boring design

```html
<!DOCTYPE html>
<html lang="en">
<head>
<meta charset="utf-8">
<title>Kelvor Engineers – Business Card</title>
<link rel="stylesheet" href="https://fonts.googleapis.com/css2?family=Roboto+Condensed:wght@700&family=Roboto:wght@400&display=swap">
<style>
  :root {
    --stage: #262626;
    --card-white: #f4f4f4;
    --navy: #012e5f;
    --navy-light: #1d4a7c;
    --lime: #22f21a;
    --ink-grey: #555555;
    --white: #ffffff;
  }
  * { margin: 0; padding: 0; box-sizing: border-box; }
  html, body {
    width: 1200px; height: 960px; overflow: hidden;
    background: var(--stage);
  }
  .canvas { position: relative; width: 1200px; height: 960px; }

  .card {
    position: absolute; left: 320px; width: 600px; height: 344px;
    border-radius: 22px; overflow: hidden;
  }

  /* Front */
  .card--front { top: 102px; background: var(--card-white); }
  .brand-name {
    position: absolute; top: 132px; left: 0; width: 100%;
    text-align: center;
    font-family: "Roboto Condensed", sans-serif; font-weight: 700;
    font-size: 60px; line-height: 1; color: var(--lime);
    letter-spacing: 0.5px;
  }
  .tagline {
    position: absolute; top: 272px; left: 0; width: 100%;
    display: flex; align-items: center; justify-content: center; gap: 4px;
    font-family: "Roboto Condensed", sans-serif; font-weight: 700;
    font-size: 16px; color: var(--lime);
  }
  .tagline__rule { width: 30px; height: 2px; background: var(--navy); }
  .locations {
    position: absolute; top: 293px; left: 0; width: 100%;
    text-align: center;
    font-family: "Roboto", sans-serif; font-size: 15px;
    letter-spacing: 0.6px; color: var(--ink-grey);
  }

  /* Back */
  .card--back { top: 493px; }
  .card__backdrop { position: absolute; inset: 0; }
  .contact {
    position: absolute; top: 72px; left: 0; width: 100%;
    text-align: center;
  }
  .contact__name {
    font-family: "Roboto Condensed", sans-serif; font-weight: 700;
    font-size: 22px; color: var(--lime); margin-bottom: 14px;
    text-transform: uppercase;
  }
  .contact__item {
    display: flex; flex-direction: column; align-items: center;
    font-family: "Roboto", sans-serif; font-size: 15px;
    color: var(--white); line-height: 18px; margin-bottom: 2px;
  }
  .contact__icon { width: 14px; height: 14px; fill: var(--lime); margin-bottom: 4px; }
</style>
</head>
<body>
<main class="canvas">

  <section class="card card--front" aria-label="Card front">
    <p class="brand-name">Kelvor Engineers</p>
    <p class="tagline"><span class="tagline__rule"></span>MULTI-DISCIPLINE ENGINEERING<span class="tagline__rule"></span></p>
    <p class="locations">Atlanta | Charlotte | Houston | San Antonio</p>
  </section>

  <section class="card card--back" aria-label="Card back">
    <svg class="card__backdrop" viewBox="0 0 600 344" role="img" aria-label="Navy sunburst background" preserveAspectRatio="none">
      <defs>
        <radialGradient id="burst" cx="50%" cy="50%" r="65%">
          <stop offset="0%" stop-color="#0a3366"/>
          <stop offset="100%" stop-color="#1a4676"/>
        </radialGradient>
      </defs>
      <rect width="600" height="344" fill="url(#burst)"/>
    </svg>

    <div class="contact">
      <h1 class="contact__name">Dana Whitlow Marsh</h1>

      <p class="contact__item">
        <svg class="contact__icon" viewBox="0 0 24 24" aria-hidden="true"><path d="M6.6 10.8a15.1 15.1 0 0 0 6.6 6.6l2.2-2.2a1 1 0 0 1 1-.25 11.4 11.4 0 0 0 3.6.57 1 1 0 0 1 1 1V20a1 1 0 0 1-1 1A17 17 0 0 1 3 4a1 1 0 0 1 1-1h3.5a1 1 0 0 1 1 1c0 1.25.2 2.45.57 3.57a1 1 0 0 1-.25 1z"/></svg>
        555.280.0142
      </p>
      <p class="contact__item">
        <svg class="contact__icon" viewBox="0 0 24 24" aria-hidden="true"><path d="M7 1h10a2 2 0 0 1 2 2v18a2 2 0 0 1-2 2H7a2 2 0 0 1-2-2V3a2 2 0 0 1 2-2zm0 3v14h10V4z"/></svg>
        555.897.0177
      </p>
      <p class="contact__item">
        <svg class="contact__icon" viewBox="0 0 24 24" aria-hidden="true"><path d="M2 5h20v14H2zm2 2v.5l8 5 8-5V7z"/></svg>
        dmarsh@kelvorstruct.com
      </p>
      <p class="contact__item">
        <svg class="contact__icon" viewBox="0 0 24 24" aria-hidden="true"><circle cx="12" cy="12" r="10"/></svg>
        www.kelvorstruct.com
      </p>
    </div>
  </section>

</main>
</body>
</html>
```